Keystonery Billboard - Financial Services Company (Investments, Tax Planning and Insurance)

Our new office has a billboard directly above the office building. We'd like something eye-catching with a strong Call to Action, with the main part of the billboard being under 7 words if possible. We'd like you to include a way to get ahold of us (either our website keystoneryllc.example or our phone number 302-418-2907. You may also include in small font something to indicate that we've been serving the area since 1980 (the DE area, the tri-state area, the Marlowe Hollow, etc.)

We offer financial planning, tax planning, and insurance, and we help our clients to focus on their goals and happiness by providing everything they need for lifelong wealth under one roof.

Our logos are attached, we use a triangle logo with green and gray. We use the tagline "discover lasting prosperity" but this does not need to be included.

Potential ideas we have seen from other financial companies-
- the concept that the driver spends more time looking at billboards than planning for their retirement
-something along the lines of "everything you need for your finances is in this building right here" planning, investments, taxes, insurance"
-don't spend your time worrying about retirement, let us help you plan for it
-are you working for your money, or is it working for you?
- retirement takes planning, we're here to help
- ready to retire? talk to us
- need investment advice?
- need help investing?
- crossing your fingers isn't a retirement plan. we can help.
- retiring soon? you need help.

Those are just general ideas, please feel free to be creative.

brand colors:
#00b585
#00b185
#000000
#ffffff
#6d6f75
#6d6f75
#6f7074
#021712
#052e24

```html
<!DOCTYPE html>
<html lang="en">
<head>
<meta charset="utf-8">
<title>Keystonery Billboard</title>
<link href="https://fonts.googleapis.com/css2?family=Poppins:wght@400;500;600;700&display=swap" rel="stylesheet">
<style>
  :root {
    --brand-green: #00a86b;
    --brand-gray: #6d6f75;
    --band-gray: #6f7074;
    --stage: #4d4b4c;
    --white: #ffffff;
    --photo-sky: #cfdde6;
    --photo-warm: #a9b3bc;
  }
  * { margin: 0; padding: 0; box-sizing: border-box; }
  html, body { width: 1200px; height: 1200px; overflow: hidden; }
  body {
    background: var(--stage);
    font-family: "Poppins", sans-serif;
    position: relative;
  }
  .billboard {
    position: absolute;
    left: 50px; top: 325px;
    width: 1100px; height: 550px;
    background: var(--white);
    overflow: hidden;
  }
  .billboard__shapes { position: absolute; inset: 0; }
  .headline {
    position: absolute;
    left: 49px; top: 14px;
    color: var(--brand-gray);
    font-weight: 400;
    font-size: 49px;
    line-height: 51px;
    letter-spacing: -0.5px;
    text-transform: uppercase;
  }
  .headline__accent { color: var(--brand-green); font-weight: 500; }
  .call-to-action {
    position: absolute;
    left: 49px; top: 268px;
    color: var(--white);
    font-weight: 600;
    font-size: 58px;
    line-height: 61px;
    letter-spacing: -0.5px;
    text-transform: uppercase;
  }
  .brand {
    position: absolute;
    left: 49px; top: 416px;
    display: flex; align-items: center; gap: 16px;
  }
  .brand__mark { width: 62px; height: 62px; background: var(--brand-green); flex: none; }
  .brand__text { display: flex; flex-direction: column; }
  .brand__name {
    color: var(--brand-green);
    font-weight: 500;
    font-size: 52px;
    line-height: 64px;
    letter-spacing: -1px;
  }
  .brand__tagline {
    color: var(--brand-gray);
    font-size: 11px;
    line-height: 14px;
    letter-spacing: 4.6px;
    text-transform: uppercase;
    margin-top: 4px;
  }
  .contact {
    position: absolute;
    right: 72px; top: 420px;
    text-align: right;
    color: var(--brand-gray);
  }
  .contact__phone {
    display: flex; align-items: center; justify-content: flex-end; gap: 10px;
    font-weight: 600;
    font-size: 50px;
    line-height: 54px;
    letter-spacing: -1px;
  }
  .contact__phone svg { width: 34px; height: 34px; }
  .contact__web {
    font-weight: 500;
    font-size: 27px;
    line-height: 34px;
    letter-spacing: 1.5px;
  }
  .contact__web-name { color: var(--brand-green); }
  .service-note {
    position: absolute;
    left: 0; bottom: 0;
    width: 100%; height: 32px;
    background: var(--band-gray);
    color: var(--white);
    font-weight: 600;
    font-size: 13px;
    line-height: 32px;
    text-align: center;
    text-transform: uppercase;
  }
</style>
</head>
<body>
  <main class="billboard">
    <svg class="billboard__shapes" viewBox="0 0 1100 550" width="1100" height="550">
      <defs>
        <linearGradient id="photo-tone" x1="0" y1="0" x2="1" y2="1">
          <stop offset="0" stop-color="var(--photo-sky)"/>
          <stop offset="1" stop-color="var(--photo-warm)"/>
        </linearGradient>
      </defs>
      <polygon class="green-band" fill="var(--brand-green)"
        points="580,0 1100,0 1100,407 0,407 0,244 620,244"/>
      <polygon class="photo-area" role="img"
        aria-label="Photo of a smiling retired couple embracing outdoors"
        fill="url(#photo-tone)"
        points="591,0 1100,0 1100,369 652,369"/>
    </svg>

    <h1 class="headline">
      Don't spend<br>your time<br>worrying<br>about <span class="headline__accent">retirement</span>
    </h1>

    <p class="call-to-action">Let us help<br>you plan for it</p>

    <div class="brand">
      <span class="brand__mark"></span>
      <div class="brand__text">
        <div class="brand__name">Keystonery</div>
        <div class="brand__tagline">Discover lasting prosperity</div>
      </div>
    </div>

    <div class="contact">
      <div class="contact__phone">
        <svg viewBox="0 0 24 24" aria-hidden="true">
          <path fill="var(--brand-green)" d="M6.6 10.8a15.1 15.1 0 0 0 6.6 6.6l2.2-2.2c.3-.3.7-.4 1-.2 1.1.4 2.3.6 3.6.6.6 0 1 .4 1 1V20c0 .6-.4 1-1 1A17 17 0 0 1 3 4c0-.6.4-1 1-1h3.5c.6 0 1 .4 1 1 0 1.3.2 2.5.6 3.6.1.3 0 .7-.2 1z"/>
          <path fill="none" stroke="var(--brand-green)" stroke-width="1.6" stroke-linecap="round" d="M14 7a4 4 0 0 1 3 3M14 3.5a7.5 7.5 0 0 1 6.5 6.5"/>
        </svg>
        <span>302-418-2907</span>
      </div>
      <div class="contact__web">www.<span class="contact__web-name">keystoneryllc</span>.example</div>
    </div>

    <p class="service-note">Serving the area since 1980 (the DE area, the tri-state area, the Marlowe Hollow, etc.)</p>
  </main>
</body>
</html>
```